Thornvale Group needs a business card design

We need a new business card design using the logo recently selected in a logo competition on Pixel Bazaar. Our business is a consultancy specializing in aviation and energy and the winning business card design will promote an image of precision and professionalism with creativity.

Please use the logo with the name on the front of the card and use a complementary font. Make the back white with either the light grey or dark grey logo.

Target Market(s)

Senior finance and legal leaders at aviation and energy companies

Industry/Entity Type

Management Consulting

Contact Information for Business Card

Peter Castrell
President
Thornvale Group

www.thornvalegroup.example

(555) 204-6391
pc@thornvalegroup.example

Requirements
Must have
• Professional font that goes well with the logo font

```html
<!DOCTYPE html>
<html lang="en">
<head>
<meta charset="utf-8">
<title>Thornvale Group – Business Card</title>
<link href="https://fonts.googleapis.com/css2?family=Open+Sans:wght@400;600;700&display=swap" rel="stylesheet">
<style>
  :root {
    --backdrop: #e4e4e2;
    --card: #f3f3f3;
    --card-back: #f7f7f7;
    --navy: #1c4a80;
    --ink: #555a60;
    --ink-soft: #6e7378;
    --shadow: rgba(0, 0, 0, 0.14);
  }
  * { box-sizing: border-box; margin: 0; padding: 0; }
  html, body {
    width: 1200px;
    height: 900px;
    overflow: hidden;
    background: var(--backdrop);
    font-family: "Open Sans", Arial, sans-serif;
  }
  .canvas {
    width: 1200px;
    height: 900px;
    display: flex;
    flex-direction: column;
    align-items: center;
    justify-content: center;
    gap: 60px;
  }
  .card {
    position: relative;
    width: 630px;
    height: 360px;
    box-shadow: 0 6px 18px var(--shadow);
    overflow: hidden;
  }

  /* Back of card */
  .card--back { background: var(--card-back); }
  .card--back .wordmark {
    position: absolute;
    right: 70px;
    bottom: 90px;
    text-align: center;
  }

  /* Wordmark shared */
  .wordmark__name {
    display: block;
    color: var(--navy);
    font-weight: 400;
    font-size: 30px;
    letter-spacing: 0.06em;
    text-transform: uppercase;
    line-height: 1.1;
  }
  .wordmark__name--small { font-size: 24px; }

  /* Front of card */
  .card--front { background: var(--card); }
  .card--front .accent-band {
    position: absolute;
    left: 0;
    right: 0;
    bottom: 0;
    height: 12px;
    background: var(--navy);
  }
  .card--front .wordmark {
    position: absolute;
    top: 62px;
    left: 0;
    right: 0;
    text-align: center;
  }
  .person {
    position: absolute;
    left: 48px;
    top: 170px;
  }
  .person__name {
    font-weight: 700;
    font-size: 15px;
    color: var(--ink);
  }
  .person__title {
    font-size: 13px;
    color: var(--navy);
    margin-top: 2px;
  }
  .contact {
    position: absolute;
    left: 250px;
    top: 170px;
    list-style: none;
    display: flex;
    flex-direction: column;
    gap: 9px;
  }
  .contact__item {
    display: flex;
    align-items: center;
    gap: 12px;
    font-size: 14px;
    color: var(--ink-soft);
  }
  .contact__icon {
    width: 16px;
    height: 16px;
    flex: none;
  }
</style>
</head>
<body>
<main class="canvas">

  <section class="card card--back" aria-label="Card back">
    <div class="wordmark">
      <span class="wordmark__name wordmark__name--small">Thornvale Group</span>
    </div>
  </section>

  <section class="card card--front" aria-label="Card front">
    <div class="wordmark">
      <span class="wordmark__name">Thornvale Group</span>
    </div>

    <div class="person">
      <p class="person__name">Peter Castrell</p>
      <p class="person__title">President</p>
    </div>

    <ul class="contact">
      <li class="contact__item">
        <svg class="contact__icon" viewBox="0 0 16 16" aria-hidden="true">
          <path d="M4 1.5h2.2l1 3.3-1.6 1.2a8 8 0 0 0 4.4 4.4l1.2-1.6 3.3 1V12a2.5 2.5 0 0 1-2.5 2.5A11.5 11.5 0 0 1 1.5 4 2.5 2.5 0 0 1 4 1.5z" fill="var(--navy)"/>
        </svg>
        (555) 204-6391
      </li>
      <li class="contact__item">
        <svg class="contact__icon" viewBox="0 0 16 16" aria-hidden="true">
          <rect x="1.5" y="3.5" width="13" height="9" fill="none" stroke="var(--navy)" stroke-width="1.5"/>
          <path d="M1.5 3.5 8 9l6.5-5.5" fill="none" stroke="var(--navy)" stroke-width="1.5"/>
        </svg>
        pc@thornvalegroup.example
      </li>
      <li class="contact__item">
        <svg class="contact__icon" viewBox="0 0 16 16" aria-hidden="true">
          <circle cx="8" cy="8" r="6.5" fill="none" stroke="var(--navy)" stroke-width="1.4"/>
          <ellipse cx="8" cy="8" rx="2.8" ry="6.5" fill="none" stroke="var(--navy)" stroke-width="1.2"/>
          <path d="M1.5 8h13" stroke="var(--navy)" stroke-width="1.2"/>
        </svg>
        www.thornvalegroup.example
      </li>
    </ul>

    <div class="accent-band"></div>
  </section>

</main>
</body>
</html>
```